Vorn upkeep KT Solar Venture

Solar power system install
Services and maintenance
wiring, Rewinding and Renovation
Switch Board Upgrade
Power and lighting point
t doesn’t matter how much you spend on quality parts, your solar system will let you down if your design and installation are sub-par. Have your solar system tailored and installed by our Master Electrician and Bright Grid Guild Accredited team.

Target Market(s)

sales and installed

Industry/Entity Type

Solar install and retailer

Contact Information for Business Card

Name , Email, Phone Number ,Business address,

Font styles to use
Serif

Colors
0054AA
0677BA
7BADD7
CADEEF
E8F1F8

Requirements
Must have
• clear and bright
Nice to have
• new design
Should not have
• unclear pictures

```html
<!DOCTYPE html>
<html lang="en">
<head>
<meta charset="utf-8">
<title>Vorn upkeep – KT Solar Venture business card</title>
<link rel="stylesheet" href="https://fonts.googleapis.com/css2?family=Roboto:wght@400;500&display=swap">
<style>
  :root {
    --stage: #2b2b2c;
    --blue-deep: #0054aa;
    --blue-mid: #0677ba;
    --teal: #1a8a9c;
    --green: #6cb33f;
    --green-text: #8cc63f;
    --band: #e9eaeb;
    --ink: #1c1c1c;
    --white: #ffffff;
    --paper: #f1f1f1;
    --brand-blue: #1a3f8f;
    --sun: #f2b51c;
  }
  * { margin: 0; padding: 0; box-sizing: border-box; }
  html, body { width: 1200px; height: 1138px; overflow: hidden; background: var(--stage); }
  body { position: relative; font-family: "Roboto", Arial, sans-serif; }

  .card { position: absolute; border-radius: 16px; overflow: hidden; }

  /* Front */
  .card-front {
    left: 274px; top: 186px; width: 623px; height: 376px;
    background: linear-gradient(110deg, var(--blue-mid) 0%, var(--teal) 45%, var(--green) 100%);
  }
  .front-brand {
    position: absolute; left: 0; top: 80px; width: 100%;
    display: flex; align-items: center; justify-content: center; gap: 20px;
  }
  .brand-dot { width: 64px; height: 64px; border-radius: 50%; background: var(--sun); flex: none; }
  .brand-name {
    font-family: "Roboto", Arial, sans-serif; font-weight: 500;
    font-size: 27px; line-height: 34px; color: var(--white);
  }
  .service-band {
    position: absolute; left: 0; top: 240px; width: 100%; height: 72px;
    background: var(--band); color: var(--ink);
    font-size: 16.5px; line-height: 23px; text-align: center;
    display: flex; flex-direction: column; justify-content: center;
  }
  .front-web {
    position: absolute; left: 0; top: 332px; width: 100%;
    display: flex; align-items: center; justify-content: center; gap: 28px;
    color: var(--white); font-size: 16px;
  }
  .front-web .rule { width: 80px; height: 2px; background: rgba(255,255,255,.75); }

  /* Back */
  .card-back { left: 276px; top: 607px; width: 618px; height: 375px; background: var(--paper); }
  .card-back svg.back-shape { position: absolute; inset: 0; }
  .back-brand {
    position: absolute; left: 10px; top: 120px; width: 240px;
    display: flex; flex-direction: column; align-items: center; gap: 18px;
  }
  .back-brand .brand-dot { width: 80px; height: 80px; background: var(--blue-mid); }
  .back-brand .brand-name { color: var(--brand-blue); font-size: 22px; line-height: 28px; text-align: center; }
  .contact { position: absolute; left: 345px; top: 56px; color: var(--white); }
  .contact-name { color: var(--green-text); font-size: 25px; font-weight: 500; line-height: 30px; }
  .contact-role { font-size: 16px; margin-top: 4px; }
  .contact-address { font-size: 16px; line-height: 24px; margin-top: 60px; }
  .contact-list { list-style: none; margin-top: 8px; font-size: 16px; }
  .contact-list li { display: flex; align-items: center; gap: 16px; height: 24px; }
  .contact-list svg { width: 16px; height: 16px; flex: none; }
  .back-tagline { position: absolute; left: 345px; top: 327px; color: var(--white); font-size: 16px; }
</style>
</head>
<body>

<section class="card card-front" aria-label="Card front">
  <div class="front-brand">
    <span class="brand-dot" aria-hidden="true"></span>
    <div class="brand-name">Vorn upkeep KT Solar Venture</div>
  </div>
  <div class="service-band">
    <p>Solar Power System Install &nbsp;|&nbsp; Wiring, Rewinding &amp; Renovation</p>
    <p>Services &amp; Maintenance &nbsp;|&nbsp; Switch Board Upgrade &nbsp;|&nbsp; Power &amp; Lighting Point</p>
  </div>
  <div class="front-web">
    <span class="rule"></span>
    <span>www.ktsolarventure.com</span>
    <span class="rule"></span>
  </div>
</section>

<section class="card card-back" aria-label="Card back">
  <svg class="back-shape" width="618" height="375" viewBox="0 0 618 375" aria-hidden="true">
    <defs>
      <linearGradient id="backBlue" x1="0" y1="0" x2="0" y2="1">
        <stop offset="0" stop-color="#0a4f9c"/>
        <stop offset="1" stop-color="#0677ba"/>
      </linearGradient>
    </defs>
    <path d="M236,0 C318,120 318,280 244,375 L618,375 L618,0 Z" fill="#3aa535"/>
    <path d="M244,0 C330,130 322,290 262,375 L618,375 L618,0 Z" fill="url(#backBlue)"/>
    <rect x="292" y="319" width="326" height="38" fill="#6cb33f"/>
    <rect x="266" y="357" width="352" height="18" fill="#0677ba"/>
  </svg>

  <div class="back-brand">
    <span class="brand-dot" aria-hidden="true"></span>
    <div class="brand-name">Vorn upkeep<br>KT Solar Venture</div>
  </div>

  <div class="contact">
    <p class="contact-name">John Doe Smith</p>
    <p class="contact-role">Managing Director</p>
    <p class="contact-address">234 Anywhere St., Any City,<br>Any Town, US 123456</p>
    <ul class="contact-list">
      <li>
        <svg viewBox="0 0 16 16" aria-hidden="true"><path d="M2 6 Q8 1 14 6 L12 8 L10 6 L6 6 L4 8 Z M4 9 H12 V14 H4 Z" fill="#8cc63f"/></svg>
        828-111-1111
      </li>
      <li>
        <svg viewBox="0 0 16 16" aria-hidden="true"><rect x="1" y="3" width="14" height="10" fill="#8cc63f"/><path d="M1 3 L8 9 L15 3" stroke="#0a5aa6" stroke-width="1.4" fill="none"/></svg>
        john@yourwebsite.com
      </li>
      <li>
        <svg viewBox="0 0 16 16" aria-hidden="true"><circle cx="8" cy="8" r="6.5" fill="none" stroke="#8cc63f" stroke-width="1.4"/><ellipse cx="8" cy="8" rx="3" ry="6.5" fill="none" stroke="#8cc63f" stroke-width="1.2"/><path d="M1.5 8 H14.5" stroke="#8cc63f" stroke-width="1.2"/></svg>
        www.yourwebsite.com
      </li>
    </ul>
  </div>

  <p class="back-tagline">Solar power system install</p>
</section>

</body>
</html>
```